Grey Fennel Medical Website to make connecting and communicating easier

To create a unique, user-friendly, professional website for patients and professionals to access education/ information, forms, appointments, contact details, and data about us, and for us to have the capacity to link to various cloud-based platforms.
To use the logo design and colour scheme we have just sourced.

WEBSITE to be eye catching, Inspiring and alluring
- efficient and logical
- professional and trustworthy appearance
- health focus "living health matters"
- user friendly
- ability to link with cloud-based software and video conferencing tools/ telehealth
- colours- black/ white teal and ?silver

PAGES:
page 1 - Our clinic and staff, services offered, contact us- address/ map / contact details- social media connections
page 2- patients and visitors - New patient forms to complete, news and patient informtion (educatinal)
page 3 - health professionals -referral forms, research and education
page 3- online appointments
page 4 - Quick links - partners, other services
page 5- privacy policy, disclaimer

HI, Could we please extend the deadline another 5 days, so sorry just struggling with my workload to be able to keep up and I am wanting to liaise more with the designer that I will choose. I am so happy with SketchHarbor and all the designers - thank you! Thank you so much!!

Target Market(s)

Patients - mostly over 60's so the website must be minimal clicks and simple to navigate
Professionals - for education and access forms

Industry/Entity Type

Health Care

Coding

Coded - Design and coding required

Number of Pages Required

5+ page

Font styles to use
Sans Serif
Script

Colors
33b8a4
86cfc6

Requirements
Must have
• WEBSITE to be eye catching, Inspiring and alluring
- efficient and logical
- user friendly

WEBSITE - professional and user friendly
- ability to link with cloud based software and videoconferencing/ telehealth
Nice to have
• clean and crisp presentation
happy for an innovative look
room to add more services and ability to link pages and resources
Should not have
• Please ensure the website is not:
clunky
difficult to navigate
common and cheap looking

```html
<!DOCTYPE html>
<html lang="en">
<head>
<meta charset="utf-8">
<title>Grey Fennel Medical – Privacy Policy, Disclaimer</title>
<link href="https://fonts.googleapis.com/css2?family=Lexend+Exa:wght@300;400&family=Montserrat:wght@400;500;600;700&display=swap" rel="stylesheet">
<style>
  :root{
    --teal:#33b8a4;
    --teal-light:#86cfc6;
    --teal-deep:#048a7d;
    --ink:#111111;
    --body:#6b6b6b;
    --panel:#f4f4f4;
    --white:#ffffff;
    --black:#000000;
  }
  *{box-sizing:border-box;margin:0;padding:0}
  html,body{width:1200px;height:2217px;overflow:hidden;background:var(--white)}
  body{position:relative;font-family:"Montserrat",sans-serif;color:var(--body)}

  .site-header{position:absolute;top:0;left:0;width:1200px;height:90px;background:var(--white)}
  .brand{position:absolute;left:183px;top:32px;display:flex;align-items:center;gap:7px;
    font-family:"Montserrat",sans-serif;font-weight:600;font-size:14px;color:var(--teal)}
  .brand-dot{width:18px;height:18px;border-radius:50%;background:var(--teal)}
  .main-nav{position:absolute;left:499px;top:38px;display:flex;gap:41px;font-size:15px;color:#444;font-weight:400}
  .social-row{position:absolute;display:flex;gap:8px}
  .header-social{left:862px;top:32px}
  .social-dot{width:33px;height:33px;border-radius:50%;background:var(--teal-light)}

  .page-banner{position:absolute;top:90px;left:0;width:1200px;height:150px;background:var(--teal-deep);
    display:flex;align-items:center;justify-content:center}
  .page-banner h1{font-family:"Lexend Exa",sans-serif;font-weight:400;font-size:41px;color:var(--white);letter-spacing:-0.5px}

  .policy-section{position:absolute;left:0;width:1200px;padding:0 184px}
  .privacy{top:240px;height:1107px;padding-top:68px}
  .disclaimer{top:1347px;height:500px;background:var(--panel);padding-top:74px}
  .section-title{font-family:"Lexend Exa",sans-serif;font-weight:400;font-size:35px;color:var(--ink);line-height:1.1;letter-spacing:-0.5px}
  .title-rule{width:38px;height:3px;background:var(--teal);margin:24px 0 20px}
  .policy-section p{font-size:15.2px;line-height:26.3px;color:var(--body);margin-bottom:26px}
  .sub-title{font-family:"Lexend Exa",sans-serif;font-weight:400;font-size:21px;color:var(--ink);margin:0 0 12px}
  .sub-title.first{margin-top:38px}
  .policy-section p.tight{margin-bottom:12px}

  .site-footer{position:absolute;top:1847px;left:0;width:1200px;height:370px;background:var(--black);color:var(--white)}
  .footer-brand{position:absolute;left:190px;top:80px;display:flex;align-items:center;gap:8px;
    font-weight:600;font-size:16px;color:var(--teal);width:150px;line-height:1.2}
  .footer-brand .brand-dot{width:22px;height:22px;flex:none}
  .lang-select{position:absolute;left:183px;top:203px;width:140px;height:34px;border:1px solid var(--white);
    display:flex;align-items:center;justify-content:center;gap:7px;font-size:12px;font-weight:500}
  .lang-flag{width:12px;height:12px;border-radius:50%;background:#c9c9c9}
  .lang-caret{font-size:8px;margin-left:30px}
  .footer-col{position:absolute;top:74px}
  .footer-col h3{font-size:17px;font-weight:700;color:var(--white)}
  .footer-col .title-rule{width:20px;height:2px;margin:10px 0 12px}
  .quick-links{left:391px}
  .quick-links ul{list-style:none;font-size:11.5px;line-height:22.5px}
  .contact-col{left:560px}
  .contact-item{display:flex;gap:12px;font-size:10.5px;line-height:14px;margin-bottom:11px}
  .contact-item svg{flex:none;width:16px;height:16px}
  .contact-item b{font-weight:700}
  .social-col{left:772px;top:78px}
  .footer-social{position:static;gap:8px}
  .footer-social .social-dot{width:34px;height:34px;background:var(--teal)}
  .footer-bottom{position:absolute;left:183px;top:315px;width:833px;border-top:1px solid #333;
    display:flex;justify-content:space-between;padding-top:20px;font-size:11.5px}
</style>
</head>
<body>
  <header class="site-header">
    <div class="brand"><span class="brand-dot"></span>Grey Fennel Medical</div>
    <nav class="main-nav"><span>Home</span><span>Staff</span><span>Services</span><span>Contact Us</span></nav>
    <div class="social-row header-social">
      <span class="social-dot"></span><span class="social-dot"></span><span class="social-dot"></span><span class="social-dot"></span>
    </div>
  </header>

  <section class="page-banner"><h1>Privacy Policy, Disclaimer</h1></section>

  <section class="policy-section privacy">
    <h2 class="section-title">Privacy Policy</h2>
    <div class="title-rule"></div>
    <p>Lorem ipsum carrots, enhanced undergraduate developer, but they do occaecat time and vitality, such as labor and obesity. Over the years come, who nostrud exercise, the school district work unless they aliquip advantage from it. Homework if cupidatat consumer to find pleasure wants to be a football cillum he shuns pain, produces no resultant. Excepteur cupidatat blacks are not excepteur, is soothing to the soul, that is, they deserted the general duties of those who are to blame for your troubles.</p>
    <p>Lorem ipsum carrots, enhanced undergraduate developer, but they do occaecat time and vitality, such as labor and obesity. Over the years come, who nostrud exercise, the school district work unless they aliquip advantage from it. Homework if cupidatat consumer to find pleasure wants to be a football cillum he shuns pain, produces no resultant. Excepteur cupidatat blacks are not excepteur, is soothing to the soul, that is, they deserted the general duties of those who are to blame for your troubles.</p>
    <h3 class="sub-title first">Lorem Ipsum</h3>
    <p class="tight">Lorem ipsum carrots, enhanced undergraduate developer, but they do occaecat time and vitality, such as labor and obesity. Over the years come, who nostrud exercise, the school district work unless they aliquip advantage from it. Homework if cupidatat consumer to find pleasure wants to be a football cillum he shuns pain, produces no resultant. Excepteur cupidatat blacks are not excepteur, is soothing to the soul, that is, they deserted the general duties of those who are to blame for your troubles.</p>
    <h3 class="sub-title">Lorem Ipsum</h3>
    <p class="tight">Lorem ipsum carrots, enhanced undergraduate developer, but they do occaecat time and vitality, such as labor and obesity. Over the years come, who nostrud exercise, the school district work unless they aliquip advantage from it. Homework if cupidatat consumer to find pleasure wants to be a football cillum he shuns pain, produces no resultant. Excepteur cupidatat blacks are not excepteur, is soothing to the soul, that is, they deserted the general duties of those who are to blame for your troubles.</p>
    <h3 class="sub-title">Lorem Ipsum</h3>
    <p class="tight">Lorem ipsum carrots, enhanced undergraduate developer, but they do occaecat time and vitality, such as labor and obesity. Over the years come, who nostrud exercise, the school district work unless they aliquip advantage from it. Homework if cupidatat consumer to find pleasure wants to be a football cillum he shuns pain, produces no resultant. Excepteur cupidatat blacks are not excepteur, is soothing to the soul, that is, they deserted the general duties of those who are to blame for your troubles.</p>
  </section>

  <section class="policy-section disclaimer">
    <h2 class="section-title">Disclaimer</h2>
    <div class="title-rule"></div>
    <p>Lorem ipsum carrots, enhanced undergraduate developer, but they do occaecat time and vitality, such as labor and obesity. Over the years come, who nostrud exercise, the school district work unless they aliquip advantage from it. Homework if cupidatat consumer to find pleasure wants to be a football cillum he shuns pain, produces no resultant. Excepteur cupidatat blacks are not excepteur, is soothing to the soul, that is, they deserted the general duties of those who are to blame for your troubles.</p>
    <p>Lorem ipsum carrots, enhanced undergraduate developer, but they do occaecat time and vitality, such as labor and obesity. Over the years come, who nostrud exercise, the school district work unless they aliquip advantage from it. Homework if cupidatat consumer to find pleasure wants to be a football cillum he shuns pain, produces no resultant. Excepteur cupidatat blacks are not excepteur, is soothing to the soul, that is, they deserted the general duties of those who are to blame for your troubles.</p>
  </section>

  <footer class="site-footer">
    <div class="footer-brand"><span class="brand-dot"></span>Grey Fennel Medical</div>
    <div class="lang-select"><span class="lang-flag"></span>English<span class="lang-caret">▼</span></div>

    <div class="footer-col quick-links">
      <h3>Quick Links</h3>
      <div class="title-rule"></div>
      <ul><li>Home</li><li>Staff</li><li>Services</li><li>Contact Us</li><li>Patients</li><li>Health Professionals</li></ul>
    </div>

    <div class="footer-col contact-col">
      <h3>Contact Us</h3>
      <div class="title-rule"></div>
      <div class="contact-item">
        <svg viewBox="0 0 16 16"><path d="M8 1a5 5 0 0 0-5 5c0 3.6 5 9 5 9s5-5.4 5-9a5 5 0 0 0-5-5zm0 7a2 2 0 1 1 0-4 2 2 0 0 1 0 4z" fill="#fff"/></svg>
        <span>Grey Fennel Medical</span>
      </div>
      <div class="contact-item">
        <svg viewBox="0 0 16 16"><rect x="4.5" y="1" width="7" height="14" rx="1.5" fill="none" stroke="#fff" stroke-width="1.6"/><circle cx="8" cy="12.3" r="0.9" fill="#fff"/></svg>
        <span><b>Call Us:</b><br>01234567890</span>
      </div>
      <div class="contact-item">
        <svg viewBox="0 0 16 16"><rect x="1" y="3.5" width="14" height="9" fill="none" stroke="#fff" stroke-width="1.4"/><path d="M1 3.5l7 5.5 7-5.5" fill="none" stroke="#fff" stroke-width="1.4"/></svg>
        <span><b>Email Us:</b><br>hello@greyfennelmedical.com</span>
      </div>
    </div>

    <div class="footer-col social-col">
      <h3>Get Social</h3>
      <div class="title-rule"></div>
      <div class="social-row footer-social">
        <span class="social-dot"></span><span class="social-dot"></span><span class="social-dot"></span><span class="social-dot"></span>
      </div>
    </div>

    <div class="footer-bottom">
      <span>Copyright © Grey Fennel Medical 2020. All right Reserved</span>
      <span>Privacy Policy, Disclaimer</span>
    </div>
  </footer>
</body>
</html>
```